Business Card Design

We are a commercial real estate brokerage in San Francisco, leasing office buildings downtown.
I would like a clean, elegant look. Simple but powerful .

Industry/Entity Type

Business

Contact Information for Business Card

Derek Holloway
lic# 07258143
415.555.0172
derek@velt-commercial.example
velt-commercial.example

```html
<!DOCTYPE html>
<html lang="en">
<head>
<meta charset="utf-8">
<title>VELT Commercial – Business Card</title>
<link href="https://fonts.googleapis.com/css2?family=Open+Sans:wght@400;600;700&display=swap" rel="stylesheet">
<style>
  :root {
    --bg: #e4e4e2;
    --card: #eef0f1;
    --slate: #565b60;
    --steel: #7086a9;
    --ink: #3f4448;
    --muted: #d9dcdf;
  }
  * { margin: 0; padding: 0; box-sizing: border-box; }
  html, body { width: 1200px; height: 768px; overflow: hidden; }
  body {
    background: var(--bg);
    font-family: "Open Sans", Arial, sans-serif;
    color: var(--ink);
    position: relative;
  }
  .card {
    position: absolute;
    width: 500px;
    height: 286px;
    background: var(--card);
    box-shadow: 0 6px 18px rgba(0,0,0,.18);
    overflow: hidden;
  }
  .card--front { left: 70px; top: 241px; }
  .card--back { left: 630px; top: 241px; }

  .brand {
    position: absolute;
    display: flex;
    align-items: center;
    gap: 14px;
    color: var(--steel);
    font-weight: 700;
    line-height: 1;
  }
  .brand__mark {
    width: 58px; height: 58px;
    background: var(--slate);
  }
  .brand__name { display: flex; flex-direction: column; }
  .brand__title { font-size: 46px; letter-spacing: 1px; }
  .brand__sub { font-size: 19px; letter-spacing: 2px; margin-top: 4px; }
  .card--front .brand { left: 108px; top: 104px; }

  .card--back .brand { left: 26px; top: 68px; gap: 10px; }
  .card--back .brand__mark { width: 44px; height: 44px; }
  .card--back .brand__title { font-size: 36px; }
  .card--back .brand__sub { font-size: 15px; }

  .wave { position: absolute; inset: 0; width: 100%; height: 100%; }

  .person {
    position: absolute;
    right: 22px; top: 84px;
    text-align: right;
    color: #fff;
  }
  .person__name { font-size: 19px; font-weight: 700; }
  .person__role { font-size: 11px; color: var(--muted); margin-top: 1px; }

  .contacts {
    position: absolute;
    left: 28px; top: 172px;
    list-style: none;
    font-size: 12px;
  }
  .contacts li { display: flex; align-items: center; gap: 10px; margin-bottom: 5px; }
  .contacts svg { width: 12px; height: 12px; fill: var(--steel); flex: none; }

  .license {
    position: absolute;
    right: 26px; bottom: 22px;
    font-size: 12px;
  }
</style>
</head>
<body>

  <section class="card card--front" aria-label="Card front">
    <div class="brand">
      <span class="brand__mark"></span>
      <span class="brand__name">
        <span class="brand__title">VELT</span>
        <span class="brand__sub">COMMERCIAL</span>
      </span>
    </div>
  </section>

  <section class="card card--back" aria-label="Card back">
    <svg class="wave" viewBox="0 0 500 286" preserveAspectRatio="none" aria-hidden="true">
      <path d="M150 0 C 250 8 300 170 500 200 L500 0 Z" fill="var(--slate)"/>
      <path d="M118 0 C 230 6 290 176 500 212" fill="none" stroke="var(--steel)" stroke-width="6"/>
      <path d="M96 6 C 210 10 280 186 500 222" fill="none" stroke="var(--steel)" stroke-width="2"/>
    </svg>

    <div class="brand">
      <span class="brand__mark"></span>
      <span class="brand__name">
        <span class="brand__title">VELT</span>
        <span class="brand__sub">COMMERCIAL</span>
      </span>
    </div>

    <div class="person">
      <p class="person__name">Derek Holloway</p>
      <p class="person__role">Managing Director</p>
    </div>

    <ul class="contacts">
      <li>
        <svg viewBox="0 0 12 12"><path d="M2 1h3l1 3-1.5 1a7 7 0 0 0 2.5 2.5L8 6l3 1v3a1 1 0 0 1-1 1A9 9 0 0 1 1 2a1 1 0 0 1 1-1z"/></svg>
        415.555.0172
      </li>
      <li>
        <svg viewBox="0 0 12 12"><path d="M0 2h12v8H0z M0 2l6 4 6-4" stroke="#eef0f1" stroke-width="1"/></svg>
        derek@velt-commercial.example
      </li>
      <li>
        <svg viewBox="0 0 12 12"><circle cx="6" cy="6" r="5.5"/><path d="M0.5 6h11M6 .5c-3 3-3 8 0 11M6 .5c3 3 3 8 0 11" stroke="#eef0f1" stroke-width=".8" fill="none"/></svg>
        www.velt-commercial.example
      </li>
    </ul>

    <p class="license">LIC# 07258143</p>
  </section>

</body>
</html>
```